Corvina Dental personal information forms

We are a Dental Practice that require an update to our information forms, there are 3 versions of it.
I will attach our old ones, we need to keep the same information on there, we just want them to look better and use our current logo and colours.
Our website is www.corvinadental.net
Our facebook is www.friendspage.net/corvinadental/
..................................................................................................

Target Market(s)

Everyone, easy to read

Industry/Entity Type

Dental Clinic

Colors
0692cd
34a6d7
cee9f5
ffffff
0255a3
3276b5

Requirements
Must have
• Logo
• Our colours
• same information as the uploaded versions
Should not have
• any other colour besides the blues, black and white

```html
<!DOCTYPE html>
<html lang="en">
<head>
<meta charset="utf-8">
<title>Corvina Dental – Personal Information Forms</title>
<link rel="stylesheet" href="https://fonts.googleapis.com/css2?family=Open+Sans:wght@400;600;700&display=swap">
<style>
:root{
  --blue-deep:#0255a3;
  --blue-mid:#3276b5;
  --blue:#0692cd;
  --blue-light:#34a6d7;
  --blue-pale:#cee9f5;
  --white:#ffffff;
  --ink:#1a1a1a;
  --rule:#9aa7b3;
  --board:#a9a9a9;
}
*{box-sizing:border-box;margin:0;padding:0}
html,body{width:891px;height:1200px;overflow:hidden}
body{
  background:radial-gradient(ellipse at center,#c4c4c4 0%,var(--board) 70%,#959595 100%);
  font-family:"Open Sans",Arial,sans-serif;color:var(--ink);position:relative;
}
.page{
  position:absolute;background:var(--white);overflow:hidden;
  box-shadow:0 2px 6px rgba(0,0,0,.35);font-size:5.6px;line-height:1.45;
  display:flex;flex-direction:column;
}
.page-1{left:36px;top:36px;width:394px;height:560px}
.page-3{left:461px;top:36px;width:394px;height:560px}
.page-2-front{left:36px;top:664px;width:394px;height:466px}
.page-2-back{left:461px;top:664px;width:394px;height:466px}
.label{position:absolute;font-size:22px;font-weight:700;color:var(--ink)}
.label-1{left:222px;top:608px}
.label-3{left:640px;top:608px}
.label-2f{left:196px;top:1142px}
.label-2b{left:620px;top:1142px}

.masthead{
  background:linear-gradient(180deg,var(--blue-light),var(--blue) 70%,var(--blue-deep));
  height:30px;display:flex;align-items:center;justify-content:center;flex:none;
}
.brand{color:var(--white);font-weight:700;font-size:13px;letter-spacing:.3px;display:flex;align-items:center;gap:5px}
.brand-dot{width:7px;height:7px;border-radius:50%;background:var(--white)}
.content{padding:10px 16px 8px;flex:1;display:flex;flex-direction:column;gap:6px;min-height:0}
.footer{
  flex:none;background:linear-gradient(180deg,var(--blue),var(--blue-deep));
  color:var(--white);padding:4px 16px;font-size:4.8px;display:flex;justify-content:space-between;
}
.footer-top{height:4px;background:var(--blue-light);flex:none}
.practitioner{display:flex;justify-content:space-between;align-items:flex-start}
.practitioner strong{display:block;font-size:6.2px;color:var(--blue-deep)}
.fill-line{display:inline-block;border-bottom:.6px solid var(--rule);min-width:60px;height:6px;vertical-align:bottom}
.title{font-size:7.4px;font-weight:700;color:var(--blue-deep)}
.intro{font-weight:600}
.intro b{color:var(--blue-deep)}
.question{display:flex;justify-content:space-between;gap:8px;border-bottom:.6px solid var(--rule);padding-bottom:3px}
.question span:last-child{font-weight:700;color:var(--blue-deep);white-space:nowrap}
.checklist{display:grid;grid-template-columns:repeat(3,1fr);gap:1.5px 8px;padding:2px 0}
.checklist li{list-style:none;display:flex;align-items:center;gap:3px}
.checklist li::before{content:"";width:4.5px;height:4.5px;border:.6px solid var(--blue-deep);flex:none}
.section-bar{background:var(--blue-deep);color:var(--white);font-weight:700;padding:1.5px 5px;font-size:5.8px}
.section-bar.pale{background:var(--blue-pale);color:var(--blue-deep)}
.details{display:grid;grid-template-columns:1fr 1fr;gap:4px 10px}
.details div{display:flex;gap:3px;border-bottom:.6px solid var(--rule);padding-bottom:1.5px}
.details div.wide{grid-column:1/3}
.details b{color:var(--blue-deep);font-weight:600;white-space:nowrap}
.details-table{border:.6px solid var(--blue-mid);display:grid;grid-template-columns:repeat(4,1fr)}
.details-table div{border-right:.6px solid var(--blue-pale);border-bottom:.6px solid var(--blue-pale);padding:1px 3px;height:10px;color:var(--blue-deep);font-weight:600}
.details-table .head{background:var(--blue-pale)}
.note{font-size:5px;color:#333}
.signature{display:flex;gap:14px;margin-top:auto}
.signature div{flex:1;border-bottom:.6px solid var(--ink);padding-top:8px;font-weight:600}
</style>
</head>
<body>

<section class="page page-1">
  <header class="masthead"><div class="brand"><span class="brand-dot"></span>Corvina Dental</div></header>
  <div class="content">
    <div class="practitioner"><div><strong>Dr Elena Marsh</strong>Dental Surgeon</div><div>Appointment date <span class="fill-line"></span></div></div>
    <p class="title">Welcome to our practice</p>
    <p class="intro"><b>YOUR INFORMATION IS CONFIDENTIAL</b> and is required so that we can offer you <b>THE BEST POSSIBLE CARE</b>. Please complete every section and let our team know if anything changes between your visits so our records stay correct.</p>
    <div class="question"><span>Are you currently receiving treatment from a doctor or specialist for any condition?</span><span>YES / NO</span></div>
    <div class="question"><span>Are you taking any tablets, medicines or supplements at present?</span><span>YES / NO</span></div>
    <p>Have you ever had or do you currently suffer from any of the following? Please tick:</p>
    <ul class="checklist">
      <li>Asthma</li><li>Heart disease</li><li>Hepatitis</li>
      <li>Diabetes</li><li>High blood pressure</li><li>Kidney disease</li>
      <li>Epilepsy</li><li>Rheumatic fever</li><li>Bleeding disorder</li>
      <li>Arthritis</li><li>Stroke</li><li>Thyroid problems</li>
      <li>Osteoporosis</li><li>Anxiety</li><li>Other</li>
    </ul>
    <div class="question"><span>Are you allergic to any medicines, latex or other materials?</span><span>YES / NO</span></div>
    <div class="question"><span>Have you ever had a reaction to a local anaesthetic?</span><span>YES / NO</span></div>
    <div class="question"><span>Are you pregnant or breastfeeding at this time?</span><span>YES / NO</span></div>
    <div class="question"><span>Do you smoke or use any tobacco products?</span><span>YES / NO</span></div>
    <p class="note">I confirm the details above are correct to the best of my knowledge and I will tell the practice about any change.</p>
    <div class="signature"><div>Signature</div><div>Date</div></div>
  </div>
  <div class="footer-top"></div>
  <footer class="footer"><span>www.corvinadental.net</span><span>www.friendspage.net/corvinadental/</span></footer>
</section>
<span class="label label-1">1.</span>

<section class="page page-3">
  <header class="masthead"><div class="brand"><span class="brand-dot"></span>Corvina Dental</div></header>
  <div class="content">
    <div class="practitioner"><div><strong>Dr Elena Marsh</strong>Dental Surgeon</div><div>Date <span class="fill-line"></span></div></div>
    <p class="intro"><b>YOUR INFORMATION IS CONFIDENTIAL</b> and is required so that we can offer you the best possible care. Please fill in all details and ask our team if you need any help.</p>
    <div class="section-bar">Personal Details</div>
    <div class="details">
      <div><b>Surname</b></div><div><b>Title</b></div>
      <div><b>Given names</b></div><div><b>Date of birth</b></div>
      <div class="wide"><b>Address</b></div>
      <div><b>Suburb</b></div><div><b>Postcode</b></div>
      <div><b>Home phone</b></div><div><b>Mobile</b></div>
      <div class="wide"><b>Email</b></div>
      <div><b>Occupation</b></div><div><b>Health fund</b></div>
      <div><b>Emergency contact</b></div><div><b>Phone</b></div>
    </div>
    <div class="section-bar pale">Medical History</div>
    <div class="question"><span>Are you under the care of a doctor at present?</span><span>YES / NO</span></div>
    <div class="question"><span>Doctor's name and phone</span><span></span></div>
    <ul class="checklist">
      <li>Asthma</li><li>Heart disease</li><li>Hepatitis</li>
      <li>Diabetes</li><li>Blood pressure</li><li>Bleeding</li>
      <li>Epilepsy</li><li>Allergies</li><li>Other</li>
    </ul>
    <div class="question"><span>Please list any medicines you are taking</span><span></span></div>
    <div class="question"><span>Are you pregnant?</span><span>YES / NO</span></div>
    <p class="note">I consent to the treatment discussed and agree to pay all fees on the day of my visit.</p>
    <div class="signature"><div>Signature</div><div>Date</div></div>
  </div>
  <div class="footer-top"></div>
  <footer class="footer"><span>www.corvinadental.net</span><span>www.friendspage.net/corvinadental/</span></footer>
</section>
<span class="label label-3">3.</span>

<section class="page page-2-front">
  <header class="masthead"><div class="brand"><span class="brand-dot"></span>Corvina Dental</div></header>
  <div class="content">
    <div class="practitioner"><div><strong>Dr Elena Marsh</strong>Dental Surgeon</div><div>Date <span class="fill-line"></span></div></div>
    <p class="intro"><b>YOUR INFORMATION IS CONFIDENTIAL.</b> Please complete both sides of this form before your appointment.</p>
    <div class="details-table">
      <div class="head">Surname</div><div></div><div class="head">Title</div><div></div>
      <div class="head">Given names</div><div></div><div class="head">Birth date</div><div></div>
      <div class="head">Address</div><div></div><div class="head">Postcode</div><div></div>
      <div class="head">Home phone</div><div></div><div class="head">Mobile</div><div></div>
      <div class="head">Email</div><div></div><div class="head">Occupation</div><div></div>
      <div class="head">Health fund</div><div></div><div class="head">Member no.</div><div></div>
    </div>
    <div class="section-bar">Medical History</div>
    <div class="details">
      <div><b>Doctor</b></div><div><b>Phone</b></div>
      <div class="wide"><b>Practice address</b></div>
    </div>
    <div class="question"><span>Are you currently receiving medical treatment?</span><span>YES / NO</span></div>
    <div class="question"><span>Have you been in hospital in the last two years?</span><span>YES / NO</span></div>
    <div class="question"><span>Are you taking blood thinning medicine?</span><span>YES / NO</span></div>
    <p>How did you hear about us?&nbsp; Friend &nbsp; Website &nbsp; Social page &nbsp; Other</p>
    <div class="question"><span>Who may we thank for referring you?</span><span></span></div>
  </div>
  <div class="footer-top"></div>
  <footer class="footer"><span>www.corvinadental.net</span><span>Please turn over</span></footer>
</section>
<span class="label label-2f">2_front</span>

<section class="page page-2-back">
  <div class="content">
    <p class="intro">Do you suffer from any of the conditions below? Please tick every box that applies to you.</p>
    <ul class="checklist">
      <li>Asthma</li><li>Heart disease</li><li>Hepatitis</li>
      <li>Diabetes</li><li>High blood pressure</li><li>Kidney disease</li>
      <li>Epilepsy</li><li>Rheumatic fever</li><li>Bleeding disorder</li>
      <li>Arthritis</li><li>Stroke</li><li>Thyroid problems</li>
    </ul>
    <div class="question"><span>Are you allergic to any medicines or materials?</span><span>YES / NO</span></div>
    <div class="question"><span>Are you pregnant or breastfeeding?</span><span>YES / NO</span></div>
    <p>Have you ever had or do you have any of the following? Please tick:</p>
    <ul class="checklist">
      <li>Joint replacement</li><li>Heart valve</li><li>Pacemaker</li>
      <li>Cancer treatment</li><li>Radiation therapy</li><li>Other</li>
    </ul>
    <div class="question"><span>Do you smoke?</span><span>YES / NO</span></div>
    <div class="question"><span>Is there anything else we should know?</span><span></span></div>
    <p class="note">I confirm the information I have given is correct. I understand fees are payable on the day and I consent to the care explained to me by the dentist.</p>
    <p class="note">Cancellations need one full working day of notice or a fee may apply.</p>
    <div class="signature"><div>Signature</div><div>Date</div></div>
  </div>
  <div class="footer-top"></div>
  <footer class="footer"><span>www.corvinadental.net</span><span>www.friendspage.net/corvinadental/</span></footer>
</section>
<span class="label label-2b">2_back</span>

</body>
</html>
```